Professional & attention grabbing.

A business card design, front and back. I already have a logo I will attach, but I am open to something new as well.
Things to include:
Name:
Title:
Phone:
Email:
Wanting something that is professional but attention grabbing.
Also we do a lot of work using drones on natural gas pipelines (leading the future)if you want to include any of that. I'm open to ideas.
Target Market(s)
Natural gas transmission industry / greenhouse gas mitigation industry
Industry/Entity Type
Business
Colors
Designer to choose colors to be used in the design.
Look and feel
Each slider illustrates characteristics of the customer's brand and the style your logo design should communicate.

```html
<!DOCTYPE html>
<html lang="en">
<head>
<meta charset="utf-8">
<title>Korval Inspections – Business Card</title>
<link href="https://fonts.googleapis.com/css2?family=Roboto:wght@400;500;700&display=swap" rel="stylesheet">
<style>
  :root {
    --backdrop: #2a2a2a;
    --card: #ffffff;
    --ink: #3a3a3c;
    --accent: #c8202a;
    --muted: #555558;
  }
  html, body {
    margin: 0;
    padding: 0;
    width: 1200px;
    height: 1000px;
    overflow: hidden;
    background: var(--backdrop);
    font-family: "Roboto", Arial, sans-serif;
  }
  .canvas {
    position: relative;
    width: 1200px;
    height: 1000px;
  }
  .card {
    position: absolute;
    left: 300px;
    width: 600px;
    height: 343px;
    background: var(--card);
    border-radius: 26px;
    box-shadow: 0 10px 30px rgba(0,0,0,0.45);
  }
  .card--front { top: 110px; }
  .card--back  { top: 520px; }

  .brand {
    display: flex;
    align-items: center;
    gap: 12px;
  }
  .brand__mark {
    width: 30px;
    height: 30px;
    background: var(--accent);
  }
  .brand__name {
    font-weight: 700;
    color: var(--ink);
    font-size: 34px;
    letter-spacing: 0.5px;
    text-transform: uppercase;
  }

  .card--front .brand {
    position: absolute;
    top: 50%;
    left: 50%;
    transform: translate(-50%, -50%);
  }

  .card--back .brand {
    position: absolute;
    left: 44px;
    top: 150px;
  }
  .card--back .brand__mark { width: 22px; height: 22px; }
  .card--back .brand__name { font-size: 22px; }

  .divider {
    position: absolute;
    left: 340px;
    top: 118px;
    width: 2px;
    height: 108px;
    background: var(--accent);
  }
  .contact {
    position: absolute;
    left: 360px;
    top: 118px;
  }
  .contact__name {
    margin: 0;
    color: var(--accent);
    font-weight: 700;
    font-size: 21px;
    letter-spacing: 0.3px;
    text-transform: uppercase;
  }
  .contact__title {
    margin: 4px 0 14px;
    color: var(--ink);
    font-weight: 500;
    font-size: 14px;
    text-transform: uppercase;
  }
  .contact__line {
    display: flex;
    align-items: center;
    gap: 10px;
    color: var(--muted);
    font-size: 15px;
    margin: 0 0 6px;
  }
  .contact__icon { width: 12px; height: 12px; flex: none; }
</style>
</head>
<body>
<main class="canvas">
  <section class="card card--front" aria-label="Card front">
    <div class="brand">
      <span class="brand__mark"></span>
      <span class="brand__name">Korval Inspections</span>
    </div>
  </section>

  <section class="card card--back" aria-label="Card back">
    <div class="brand">
      <span class="brand__mark"></span>
      <span class="brand__name">Korval Inspections</span>
    </div>
    <div class="divider"></div>
    <div class="contact">
      <h2 class="contact__name">Daniel Reyes</h2>
      <p class="contact__title">Founder</p>
      <p class="contact__line">
        <svg class="contact__icon" viewBox="0 0 12 12" aria-hidden="true">
          <path d="M2 1.5h2.2l1 2.6-1.3.9a6.5 6.5 0 0 0 3.1 3.1l.9-1.3 2.6 1V10a1 1 0 0 1-1 1A9.5 9.5 0 0 1 1 2.5a1 1 0 0 1 1-1z" fill="#c8202a"/>
        </svg>
        000 000 0000
      </p>
      <p class="contact__line">
        <svg class="contact__icon" viewBox="0 0 12 12" aria-hidden="true">
          <rect x="0.5" y="2" width="11" height="8" fill="#c8202a"/>
          <path d="M0.8 2.4 6 6.6l5.2-4.2" fill="none" stroke="#ffffff" stroke-width="1"/>
        </svg>
        info@yourmail.com
      </p>
    </div>
  </section>
</main>
</body>
</html>
```